Corvane Capital Business Cards

These are professional business cards that are for my family office.
Put fake emails and phone numbers as of now until I finalize those components. This family office controls my families investments, assets, and future. The cards should be professional.
..
.
.
.
I just uploaded another variation of a logo I would like to see as a business card to I am inbeteen which logo to use

Target Market(s)

business

Industry/Entity Type

business

Contact Information for Business Card

Professional, wealth related, finance related.

Requirements
Must have
• Logo

```html
<!DOCTYPE html>
<html lang="en">
<head>
<meta charset="utf-8">
<title>Corvane Capital Business Cards</title>
<link rel="stylesheet" href="https://fonts.googleapis.com/css2?family=Montserrat:wght@600&family=Roboto:wght@400&display=swap">
<style>
  :root {
    --backdrop: #d1d2d4;
    --card-front: #f1f2f4;
    --ink: #1b2030;
    --ink-soft: #4f535a;
    --rule: #b4b5b8;
    --navy-deep: #0d121b;
    --navy: #171d2a;
  }
  html, body {
    margin: 0;
    width: 1200px;
    height: 1000px;
    overflow: hidden;
    background: var(--backdrop);
  }
  .canvas {
    position: relative;
    width: 1200px;
    height: 1000px;
  }
  .card {
    position: absolute;
    left: 298px;
    width: 602px;
    height: 344px;
  }
  .card-front {
    top: 143px;
    background: var(--card-front);
  }
  .card-back {
    top: 512px;
    width: 603px;
    height: 345px;
    background: radial-gradient(ellipse at 20% 20%, #2a303b 0%, var(--navy) 45%, var(--navy-deep) 100%);
  }
  .wordmark {
    position: absolute;
    right: 54px;
    top: 60px;
    margin: 0;
    font-family: "Montserrat", sans-serif;
    font-weight: 600;
    font-size: 30px;
    letter-spacing: 1px;
    color: var(--ink);
    white-space: nowrap;
  }
  .person {
    position: absolute;
    left: 48px;
    top: 121px;
  }
  .person-name {
    margin: 0;
    font-family: "Montserrat", sans-serif;
    font-weight: 600;
    font-size: 18px;
    letter-spacing: 0.3px;
    color: var(--ink);
    line-height: 22px;
  }
  .person-title {
    margin: 0;
    font-family: "Roboto", sans-serif;
    font-size: 15px;
    color: var(--ink-soft);
    line-height: 20px;
  }
  .contact-list {
    position: absolute;
    left: 48px;
    top: 182px;
    margin: 0;
    padding: 0;
    list-style: none;
    font-family: "Roboto", sans-serif;
    font-size: 15px;
    color: var(--ink-soft);
  }
  .contact-list li {
    display: flex;
    align-items: center;
    height: 20.5px;
  }
  .contact-icon {
    width: 14px;
    height: 14px;
    margin-right: 8px;
    fill: var(--ink);
  }
  .divider {
    position: absolute;
    left: 48px;
    top: 257px;
    width: 500px;
    height: 1px;
    background: var(--rule);
  }
  .address {
    position: absolute;
    left: 48px;
    top: 271px;
    display: flex;
    align-items: center;
    font-family: "Roboto", sans-serif;
    font-size: 15px;
    color: var(--ink-soft);
    white-space: nowrap;
  }
  .address .contact-icon {
    width: 12px;
    height: 17px;
    margin-right: 8px;
  }
</style>
</head>
<body>
<main class="canvas">
  <section class="card card-front" aria-label="Business card front">
    <h1 class="wordmark">Corvane Capital</h1>

    <div class="person">
      <p class="person-name">DANIEL HARROW</p>
      <p class="person-title">Managing Director</p>
    </div>

    <ul class="contact-list">
      <li>
        <svg class="contact-icon" viewBox="0 0 16 16" aria-hidden="true"><path d="M1 5c0-2 3-3 7-3s7 1 7 3v1.5h-3.5V5h-7v1.5H1zM3 8l2-2h6l2 2v6H3zm5 1.2a2 2 0 1 0 0 4 2 2 0 0 0 0-4z"/></svg>
        (555) 214-7XXX
      </li>
      <li>
        <svg class="contact-icon" viewBox="0 0 16 16" aria-hidden="true"><path d="M1 3h14v1.2L8 9 1 4.2zm0 2.6 7 4.8 7-4.8V13H1z"/></svg>
        info@corvanecapital.com
      </li>
      <li>
        <svg class="contact-icon" viewBox="0 0 16 16" aria-hidden="true"><path d="M8 1a7 7 0 1 0 0 14A7 7 0 0 0 8 1zm-1 2.3L8.5 5 7 7 4.5 6.2 3.4 8A4.8 4.8 0 0 1 7 3.3zM9.5 12.6 9 10l2-1.5 1.7 1.8a5 5 0 0 1-3.2 2.3z"/></svg>
        www.corvanecapital.com
      </li>
    </ul>

    <div class="divider"></div>

    <p class="address">
      <svg class="contact-icon" viewBox="0 0 12 17" aria-hidden="true"><path d="M6 0a6 6 0 0 0-6 6c0 4.5 6 11 6 11s6-6.5 6-11a6 6 0 0 0-6-6zm0 8.3a2.3 2.3 0 1 1 0-4.6 2.3 2.3 0 0 1 0 4.6z"/></svg>
      480 Larkspur Ave Suite 220, Marlow Bay, 90000 California / USA
    </p>
  </section>

  <section class="card card-back" role="img" aria-label="Card back: dark navy field with a repeating embossed monogram pattern"></section>
</main>
</body>
</html>
```